Vibrant, yet professional, stationery set and other designs required.

I need to source a fantastic designer for a new project as part of my company using a new logo designed via sketch harbor.

**UPDATE** I am not looking for just 'fine' design that will suffice. I am looking for something great.

We are a life assurance brokerage based in Dublin, Ireland and BrightRoost.ie is our new website aimed at providing services for young families in Ireland. We are hoping to be the 'Velro' level of service providers in this area and I am looking for the quality of design to reflect this :-) Hopefully that makes sense!

I have a preference for straight lines over curves and waves.

I need...

1. Business card
2. Letterhead
3. Banner (for printing - 76cm X 305cm)
4. Car branding for KORVA 9 (2014 sport model) I believe the templates are freely available online.

Target Market(s)

Parents in Ireland - Aged 27 to 50.

Industry/Entity Type

Financial Planning

Colors

Designer to choose colors to be used in the design.

Requirements
Must have
• All of the items listed in the description above. I like clean, bright, legible, vibrant and professional design.
Should not have
• No silly or 'cheap' looking designs. This is a professional company looking to provide a professional service.

```html
<!DOCTYPE html>
<html lang="en">
<head>
<meta charset="utf-8">
<title>BrightRoost.ie — Business Card</title>
<link href="https://fonts.googleapis.com/css2?family=Roboto:wght@400;500;700&display=swap" rel="stylesheet">
<style>
  :root {
    --backdrop: #c9c9c9;
    --orange: #f08119;
    --slate: #8b9599;
    --green: #8dc13f;
    --sky: #6cc5e0;
    --paper: #f4f4f3;
    --ink: #555b5e;
    --white: #ffffff;
  }
  * { margin: 0; padding: 0; box-sizing: border-box; }
  html, body {
    width: 1200px; height: 960px; overflow: hidden;
    background: var(--backdrop);
    font-family: "Roboto", Arial, sans-serif;
  }
  .canvas { position: relative; width: 1200px; height: 960px; }

  .card { position: absolute; left: 320px; width: 600px; overflow: hidden; }

  /* Front */
  .card-front {
    top: 110px; height: 330px;
    background: var(--orange);
    display: flex; align-items: center; justify-content: center;
  }
  .brand-front {
    display: flex; align-items: center; gap: 14px;
    color: var(--white); font-weight: 700; font-size: 54px; letter-spacing: -0.5px;
  }
  .brand-dot { width: 18px; height: 18px; border-radius: 50%; background: var(--white); }

  /* Back */
  .card-back {
    top: 493px; height: 343px;
    background: var(--paper);
  }
  .brand-back {
    position: absolute; left: 60px; top: 148px;
    display: flex; align-items: center; gap: 8px;
    color: var(--slate); font-weight: 700; font-size: 32px; letter-spacing: -0.3px;
  }
  .brand-back .brand-dot { width: 12px; height: 12px; background: var(--orange); }
  .divider {
    position: absolute; left: 328px; top: 77px;
    width: 1px; height: 183px; background: var(--ink);
  }
  .contact { position: absolute; left: 354px; top: 76px; color: var(--ink); }
  .contact-name { color: var(--orange); font-weight: 500; font-size: 19px; line-height: 24px; }
  .contact-role { color: var(--slate); font-weight: 500; font-size: 15px; line-height: 22px; margin-bottom: 9px; }
  .contact-lines { font-size: 15px; line-height: 19px; }
  .contact-lines + .contact-lines { margin-top: 7px; }
  .contact-web { font-weight: 700; letter-spacing: 1.2px; }

  .footer-band {
    position: absolute; left: 0; bottom: 0; width: 600px; height: 22px;
    background: linear-gradient(90deg, var(--slate), var(--sky));
  }
</style>
</head>
<body>
<main class="canvas">
  <section class="card card-front" aria-label="Business card front">
    <div class="brand-front"><span class="brand-dot"></span>BrightRoost.ie</div>
  </section>

  <section class="card card-back" aria-label="Business card back">
    <div class="brand-back"><span class="brand-dot"></span>BrightRoost.ie</div>
    <div class="divider"></div>
    <div class="contact">
      <p class="contact-name">AOIFE BRENNAN</p>
      <p class="contact-role">CEO/FOUNDER</p>
      <div class="contact-lines">
        <p>4128 Larkspur Way</p>
        <p>Ranelagh, Dublin D06 K2P8</p>
      </div>
      <div class="contact-lines">
        <p>(P) 612 555 0148</p>
        <p>(M) 847 555 0293</p>
        <p>(F) 473 555 0716</p>
        <p>aoife@brightroost.ie</p>
        <p class="contact-web">www.brightroost.ie</p>
      </div>
    </div>
    <div class="footer-band" role="img" aria-label="Decorative colour band along the bottom edge of the card"></div>
  </section>
</main>
</body>
</html>
```